Business Card for Lantern Reach

Please design a Modern Business card for a Online Marketing Company

Website: http://www.lanternreach-example.com.au

Please do NOT include physical address in design.

```html
<!DOCTYPE html>
<html lang="en">
<head>
<meta charset="utf-8">
<title>Lantern Reach – Business Card</title>
<link rel="stylesheet" href="https://fonts.googleapis.com/css2?family=Roboto:wght@400;700;900&family=Open+Sans:wght@400;600&display=swap">
<style>
  :root {
    --brand-red: #c40f1d;
    --brand-red-dark: #a30c17;
    --brand-orange: #f39200;
    --ink: #1a1a1a;
    --paper: #ffffff;
    --stage: #ece9e4;
  }
  * { box-sizing: border-box; margin: 0; padding: 0; }
  html, body { width: 1200px; height: 584px; overflow: hidden; }
  body {
    background: var(--stage);
    position: relative;
    font-family: "Open Sans", sans-serif;
  }
  .card {
    position: absolute;
    top: 137px;
    width: 540px;
    height: 310px;
    border-radius: 24px;
    overflow: hidden;
    box-shadow: 0 6px 18px rgba(0,0,0,0.18);
  }
  .card--front { left: 40px; background: var(--paper); }
  .card--back  { left: 620px; background: var(--brand-red); color: var(--paper); }

  .front-band { position: absolute; inset: 0; width: 100%; height: 100%; }

  .brand {
    position: absolute;
    left: 34px;
    top: 70px;
  }
  .brand__row { display: flex; align-items: center; gap: 10px; }
  .brand__square {
    width: 20px; height: 20px;
    background: var(--brand-red);
    border-radius: 4px;
  }
  .brand__name {
    font-family: "Roboto", sans-serif;
    font-weight: 900;
    font-size: 22px;
    color: var(--brand-red);
    letter-spacing: 0.2px;
  }
  .brand__tagline {
    font-family: "Roboto", sans-serif;
    font-weight: 700;
    font-size: 12px;
    color: var(--ink);
    margin-top: 2px;
    margin-left: 30px;
  }

  .person { position: absolute; left: 34px; top: 178px; }
  .person__name {
    font-family: "Roboto", sans-serif;
    font-weight: 700;
    font-size: 20px;
    color: var(--brand-red);
  }
  .person__title {
    font-family: "Roboto", sans-serif;
    font-size: 14px;
    color: var(--brand-orange);
    margin-top: -2px;
  }
  .contacts { list-style: none; margin-top: 10px; }
  .contacts__item {
    display: flex; align-items: center; gap: 8px;
    font-size: 12.5px; color: var(--ink);
    line-height: 21px;
  }
  .contacts__icon { width: 12px; height: 12px; fill: var(--brand-red); flex: none; }

  .back-content {
    position: absolute; inset: 0;
    display: flex; flex-direction: column;
    align-items: center; justify-content: center;
    text-align: center;
  }
  .back-content__name {
    font-family: "Roboto", sans-serif;
    font-weight: 900;
    font-size: 40px;
    letter-spacing: 0.5px;
    margin-top: -30px;
  }
  .back-content__tagline {
    font-family: "Roboto", sans-serif;
    font-weight: 700;
    font-size: 20px;
  }
  .back-content__web {
    font-size: 16px;
    letter-spacing: 1px;
    margin-top: 60px;
  }
</style>
</head>
<body>
  <section class="card card--front" aria-label="Business card front">
    <svg class="front-band" viewBox="0 0 540 310" preserveAspectRatio="none" aria-hidden="true">
      <polygon points="430,0 540,0 540,310 470,310 400,210 470,120" fill="var(--brand-red)"/>
      <polygon points="445,0 465,0 488,120 418,210 490,310 478,310 405,210 475,120" fill="var(--brand-red-dark)" opacity="0.35"/>
    </svg>

    <div class="brand">
      <div class="brand__row">
        <span class="brand__square"></span>
        <span class="brand__name">LANTERN REACH</span>
      </div>
      <p class="brand__tagline">Be seen online - Grow online</p>
    </div>

    <div class="person">
      <p class="person__name">Your Name</p>
      <p class="person__title">Title</p>
      <ul class="contacts">
        <li class="contacts__item">
          <svg class="contacts__icon" viewBox="0 0 24 24" aria-hidden="true"><path d="M6.6 10.8a15 15 0 0 0 6.6 6.6l2.2-2.2c.3-.3.7-.4 1-.2 1.1.4 2.3.6 3.6.6.6 0 1 .4 1 1V20c0 .6-.4 1-1 1C10.6 21 3 13.4 3 4c0-.6.4-1 1-1h3.5c.6 0 1 .4 1 1 0 1.3.2 2.5.6 3.6.1.3 0 .7-.2 1z"/></svg>
          0412 555 019
        </li>
        <li class="contacts__item">
          <svg class="contacts__icon" viewBox="0 0 24 24" aria-hidden="true"><path d="M2 5h20v14H2z M4 7v.5l8 5 8-5V7l-8 5z" fill-rule="evenodd"/></svg>
          plan@lanternreach-example.com.au
        </li>
        <li class="contacts__item">
          <svg class="contacts__icon" viewBox="0 0 24 24" aria-hidden="true"><path d="M12 2a10 10 0 1 0 0 20 10 10 0 0 0 0-20zm6.9 6h-3a15 15 0 0 0-1.3-3.9A8 8 0 0 1 18.9 8zM12 4c.8 1.2 1.5 2.5 1.9 4h-3.8c.4-1.5 1.1-2.8 1.900-4zM4.3 14a8 8 0 0 1 0-4h3.4a16 16 0 0 0 0 4zm.8 2h3a15 15 0 0 0 1.3 3.9A8 8 0 0 1 5.1 16zm3-8h-3a8 8 0 0 1 4.3-3.9A15 15 0 0 0 8.1 8zM12 20c-.8-1.2-1.5-2.5-1.9-4h3.8c-.4 1.5-1.1 2.8-1.9 4zm2.3-6H9.7a14 14 0 0 1 0-4h4.6a14 14 0 0 1 0 4zm.3 5.9a15 15 0 0 0 1.3-3.9h3a8 8 0 0 1-4.3 3.9zM16.3 14a16 16 0 0 0 0-4h3.4a8 8 0 0 1 0 4z"/></svg>
          www.lanternreach-example.com.au
        </li>
      </ul>
    </div>
  </section>

  <section class="card card--back" aria-label="Business card back">
    <div class="back-content">
      <p class="back-content__name">LANTERN REACH</p>
      <p class="back-content__tagline">Be seen online - Grow online</p>
      <p class="back-content__web">www.lanternreach-example.com.au</p>
    </div>
  </section>
</body>
</html>
```